Commercial Real Estate

We need a business card design for a new commercial real estate business that specializes in apartment building brokerage. Not individual units but the entire complex. We find and represent the owners existing buildings and well as new buyers for those buildings. The design should convey trust, integrity, knowledge and growth. It should be easily read.

Target Market(s)

40 to 65 years old

Industry/Entity Type

Real Estate

```html
<!DOCTYPE html>
<html lang="en">
<head>
<meta charset="utf-8">
<title>Halvard Estates – Business Card</title>
<link rel="stylesheet" href="https://fonts.googleapis.com/css2?family=Open+Sans:wght@400;600;700&display=swap">
<style>
  :root {
    --page-bg: #e6e7e8;
    --card-white: #ffffff;
    --card-mist: #eceeef;
    --teal: #66c4c6;
    --slate: #5d6466;
    --ink: #3f4648;
    --on-teal: #ffffff;
  }
  * { margin: 0; padding: 0; box-sizing: border-box; }
  html, body {
    width: 1038px;
    height: 1200px;
    overflow: hidden;
  }
  body {
    background: linear-gradient(180deg, #f1f2f3 0%, var(--page-bg) 100%);
    font-family: "Open Sans", Arial, sans-serif;
    position: relative;
  }
  .card {
    position: absolute;
    left: 89px;
    width: 860px;
    height: 498px;
    overflow: hidden;
    box-shadow: 0 6px 18px rgba(0,0,0,0.22), 0 1px 3px rgba(0,0,0,0.15);
  }
  .card--front {
    top: 70px;
    background: linear-gradient(115deg, var(--card-white) 0%, var(--card-mist) 70%);
  }
  .card--back {
    top: 632px;
    background: linear-gradient(125deg, var(--card-mist) 0%, var(--card-white) 45%, var(--card-white) 100%);
  }
  .card__shapes {
    position: absolute;
    inset: 0;
    width: 100%;
    height: 100%;
  }
  .brand {
    position: absolute;
    left: 64px;
    top: 228px;
    display: flex;
    align-items: center;
    gap: 14px;
  }
  .brand__square {
    width: 26px;
    height: 26px;
    background: var(--teal);
  }
  .brand__name {
    font-weight: 700;
    font-size: 36px;
    color: var(--ink);
    letter-spacing: 0.5px;
  }
  .contact {
    position: absolute;
    right: 61px;
    top: 120px;
    text-align: right;
    color: var(--on-teal);
  }
  .contact__name {
    font-weight: 700;
    font-size: 22px;
    line-height: 30px;
  }
  .contact__title {
    font-size: 17px;
    line-height: 24px;
    margin-bottom: 40px;
  }
  .contact__list {
    list-style: none;
    font-size: 17px;
  }
  .contact__item {
    display: flex;
    justify-content: flex-end;
    align-items: center;
    gap: 10px;
    height: 29px;
  }
  .contact__icon {
    width: 16px;
    height: 16px;
    flex: none;
  }
  .contact__address {
    margin-top: 22px;
    font-size: 17px;
    line-height: 29px;
  }
</style>
</head>
<body>

  <section class="card card--front" aria-label="Business card front">
    <svg class="card__shapes" viewBox="0 0 860 498" aria-hidden="true">
      <path d="M528 0 A410 410 0 0 0 604 498 L860 498 L860 0 Z" fill="#5d6466"/>
      <path d="M562 0 A400 400 0 0 0 614 498 L860 498 L860 0 Z" fill="#66c4c6"/>
    </svg>

    <div class="brand">
      <span class="brand__square"></span>
      <span class="brand__name">Halvard Estates</span>
    </div>

    <div class="contact">
      <p class="contact__name">Daniel Harrow</p>
      <p class="contact__title">Technical Director</p>
      <ul class="contact__list">
        <li class="contact__item">03 9400 2860
          <svg class="contact__icon" viewBox="0 0 16 16" aria-hidden="true"><path d="M4 1.5l2.3 2.8-1.3 1.8c.9 2 2.4 3.5 4.4 4.4l1.8-1.3 2.8 2.3-1.3 2.5C7.6 13.8 2.2 8.4 1.5 3.2z" fill="#fff"/></svg>
        </li>
        <li class="contact__item">0418 552 903
          <svg class="contact__icon" viewBox="0 0 16 16" aria-hidden="true"><rect x="4" y="1" width="8" height="14" rx="1.5" fill="none" stroke="#fff" stroke-width="1.6"/><circle cx="8" cy="12.5" r="0.9" fill="#fff"/></svg>
        </li>
        <li class="contact__item">daniel@halvardestates.com.au
          <svg class="contact__icon" viewBox="0 0 16 16" aria-hidden="true"><rect x="1.5" y="3.5" width="13" height="9" fill="#fff"/><path d="M1.5 3.5L8 9l6.5-5.5" fill="none" stroke="#66c4c6" stroke-width="1.3"/></svg>
        </li>
        <li class="contact__item">www.halvardestates.com.au
          <svg class="contact__icon" viewBox="0 0 16 16" aria-hidden="true"><circle cx="8" cy="8" r="6.5" fill="none" stroke="#fff" stroke-width="1.5"/><ellipse cx="8" cy="8" rx="2.8" ry="6.5" fill="none" stroke="#fff" stroke-width="1.2"/><path d="M1.5 8h13" stroke="#fff" stroke-width="1.2"/></svg>
        </li>
      </ul>
      <p class="contact__address">Level 2, 14 Carrow St<br>Australia Sidney</p>
    </div>
  </section>

  <section class="card card--back" aria-label="Business card back"></section>

</body>
</html>
```